KLV Plant Services

We are a heavy diesel mechanical business with additional air con certificates, remapping engine rebuilt

Contact Information for Business Card

Company Name, Director Name, Managing Director, Contact details, email and website

Font styles to use
Serif
Script

```html
<!DOCTYPE html>
<html lang="en">
<head>
<meta charset="utf-8">
<title>KLV Plant Services – Business Card</title>
<link rel="stylesheet" href="https://fonts.googleapis.com/css2?family=Arimo:wght@400;700&display=swap">
<style>
  :root {
    --page-bg: #d9d6d1;
    --card-bg: #eceae6;
    --card-edge: #b9b7b4;
    --navy: #1c1f4a;
    --text-main: #1a1a24;
    --text-soft: #2b2b33;
  }
  * { margin: 0; padding: 0; box-sizing: border-box; }
  html, body {
    width: 1170px;
    height: 1200px;
    overflow: hidden;
    background: var(--page-bg);
    font-family: "Arimo", Arial, sans-serif;
  }
  .card {
    position: absolute;
    left: 85px;
    top: 315px;
    width: 1000px;
    height: 570px;
    border-radius: 26px;
    background: var(--card-bg);
    border: 2px solid var(--card-edge);
    overflow: hidden;
  }
  .card-band {
    position: absolute;
    left: 0;
    top: 0;
  }
  .brand {
    position: absolute;
    right: 54px;
    top: 58px;
    display: flex;
    align-items: center;
    gap: 16px;
    color: var(--navy);
    font-weight: 700;
    text-align: right;
  }
  .brand-mark {
    width: 26px;
    height: 26px;
    border-radius: 50%;
    background: var(--navy);
  }
  .brand-name { line-height: 1; }
  .brand-name .brand-initials { display: block; font-size: 74px; letter-spacing: 1px; }
  .brand-name .brand-line { display: block; font-size: 24px; margin-top: 4px; }
  .details {
    position: absolute;
    right: 54px;
    top: 245px;
    text-align: right;
    color: var(--text-soft);
  }
  .person-name {
    font-size: 35px;
    font-weight: 700;
    color: var(--navy);
    line-height: 1.1;
  }
  .person-role {
    font-size: 24px;
    line-height: 1.3;
  }
  .address {
    margin-top: 24px;
    font-size: 24px;
    line-height: 32px;
    color: var(--text-main);
  }
  .contacts {
    list-style: none;
    margin-top: 22px;
    font-size: 24px;
    line-height: 31px;
    color: var(--text-main);
  }
  .contacts li {
    display: flex;
    justify-content: flex-end;
    align-items: center;
    gap: 4px;
  }
  .contacts svg { width: 20px; height: 20px; flex: none; }
</style>
</head>
<body>
  <div class="card">
    <svg class="card-band" width="1000" height="570" viewBox="0 0 1000 570" aria-hidden="true">
      <ellipse cx="-120" cy="285" rx="330" ry="320" fill="var(--navy)"/>
    </svg>

    <div class="brand">
      <span class="brand-mark"></span>
      <div class="brand-name">
        <span class="brand-initials">KLV</span>
        <span class="brand-line">Plant Services</span>
      </div>
    </div>

    <div class="details">
      <p class="person-name">Owen Hartley</p>
      <p class="person-role">Managing Director</p>
      <p class="address">2716 Halden Road<br>Brookvale, NY 11520</p>
      <ul class="contacts">
        <li>(614) 5290-3187
          <svg viewBox="0 0 24 24" aria-hidden="true"><path fill="var(--navy)" d="M6.6 10.8a15.1 15.1 0 0 0 6.6 6.6l2.2-2.2a1 1 0 0 1 1-.25 11.4 11.4 0 0 0 3.6.57 1 1 0 0 1 1 1V20a1 1 0 0 1-1 1A17 17 0 0 1 3 4a1 1 0 0 1 1-1h3.5a1 1 0 0 1 1 1c0 1.25.2 2.45.57 3.570a1 1 0 0 1-.25 1z"/></svg>
        </li>
        <li>name@KLV.com
          <svg viewBox="0 0 24 24" aria-hidden="true"><rect x="2" y="5" width="20" height="14" rx="2" fill="var(--navy)"/><path d="M3 6l9 7 9-7" fill="none" stroke="var(--card-bg)" stroke-width="1.6"/></svg>
        </li>
        <li>www.KLV.com
          <svg viewBox="0 0 24 24" aria-hidden="true"><circle cx="12" cy="12" r="10" fill="var(--navy)"/><path d="M2 12h20M12 2c3 3 3 17 0 20M12 2c-3 3-3 17 0 20" fill="none" stroke="var(--card-bg)" stroke-width="1.4"/></svg>
        </li>
      </ul>
    </div>
  </div>
</body>
</html>
```